New Business Card Design for Manufacturing

We are an engineering/manufacturing company that offers Advanced machining/assembly/engineering services, as well as innovative products for the heavy duty engine cooling markets.

We are looking to get a new business card designed that is clean and modern looking, but still fits the wide range of technical/skilled work we do.

- We hope to use this design as the base for other design work in new Presentations, web, and print work.

Industry/Entity Type

Engineering

Contact Information for Business Card

Our preferred color of blue is (RGB) 22/71/159 but can vary slightly from that color. Our content will be our Logo and full company name (Vantrell Forge Works, Inc.), company address, name, job title, phone number with extension, cell number, fax number, website, and email address on the cards.
We'd like the full company name next to the logo, but we are open to other interpretations of that layout.
Preferably, we would like the back side to be clean with just our logo, and the front to contain all of the contact information.

Colors
2f74b4
0355a3
85abd2

Requirements
Must have
• - Logo, company name, needed content - We are open to interpretation beyond that.
• - Standard size business card.
• - Horizontal orientation.
• - Enough space for lengthy names / job titles (for example, a job title could read "Directory of Human Resources" or "V.P. of Governmental Affairs"). We need this to look clean, whether the title be short (CEO) or long (as described above).

```html
<!DOCTYPE html>
<html lang="en">
<head>
<meta charset="utf-8">
<title>Vantrell Forge Works – Business Card</title>
<link href="https://fonts.googleapis.com/css2?family=Roboto:wght@400;500;700;900&family=Roboto+Condensed:wght@500&display=swap" rel="stylesheet">
<style>
  :root {
    --brand-blue: #0f50a0;
    --paper: #f2f2f2;
    --ink: #1a1a1a;
    --ink-soft: #4a4a4a;
    --tag-grey: #7d8085;
    --rule: #b5b5b5;
    --backdrop: #2b2b2b;
    --white: #ffffff;
  }
  * { margin: 0; padding: 0; box-sizing: border-box; }
  html, body {
    width: 1200px; height: 960px; overflow: hidden;
    background: var(--backdrop);
    font-family: "Roboto", Arial, sans-serif;
  }
  .canvas { position: relative; width: 1200px; height: 960px; }

  .card {
    position: absolute; width: 600px; height: 343px; overflow: hidden;
  }
  .card--front { left: 314px; top: 113px; background: var(--paper); }
  .card--back  { left: 311px; top: 472px; background: var(--brand-blue); }

  .card__bands { position: absolute; inset: 0; }
  .card__bands polygon { fill: var(--brand-blue); }

  .wordmark {
    position: absolute; left: 62px; top: 148px;
    color: var(--brand-blue);
    font-weight: 900; font-size: 45px; line-height: 1; letter-spacing: 0.5px;
  }
  .tagline {
    position: absolute; left: 64px; top: 200px;
    color: var(--tag-grey);
    font-weight: 700; font-size: 13.5px; letter-spacing: 0.2px;
    text-transform: uppercase;
  }

  .divider {
    position: absolute; left: 316px; top: 92px; width: 1px; height: 170px;
    background: var(--rule);
  }
  .divider__accent {
    position: absolute; left: 313px; top: 88px; width: 6px; height: 37px;
    background: var(--brand-blue);
  }

  .contact { position: absolute; left: 346px; top: 86px; }
  .contact__name {
    font-family: "Roboto Condensed", "Arial Narrow", sans-serif;
    font-weight: 500; font-size: 23px; color: var(--brand-blue);
    line-height: 26px; letter-spacing: 0.3px;
  }
  .contact__title { font-size: 14px; color: var(--ink); line-height: 18px; }
  .contact__address {
    margin-top: 6px; font-size: 14px; color: var(--ink-soft); line-height: 18px;
  }
  .contact__list { list-style: none; margin-top: 8px; }
  .contact__item {
    display: flex; align-items: center; gap: 8px;
    font-size: 14px; color: var(--ink-soft); height: 19.5px;
  }
  .contact__icon { width: 14px; height: 14px; flex: none; fill: var(--brand-blue); }

  .lockup {
    position: absolute; left: 107px; top: 148px;
    display: flex; align-items: flex-start; gap: 18px;
    color: var(--white);
  }
  .lockup__mark { display: flex; flex-direction: column; }
  .lockup__wordmark { font-weight: 900; font-size: 45px; line-height: 1; letter-spacing: 0.5px; }
  .lockup__tagline {
    font-weight: 700; font-size: 13.5px; text-transform: uppercase; margin-top: 8px;
  }
  .lockup__company {
    margin-top: -12px;
    font-weight: 900; font-size: 17px; line-height: 19px; text-transform: uppercase;
  }
  .lockup__suffix { font-size: 9px; margin-left: 3px; }
</style>
</head>
<body>
<main class="canvas">

  <section class="card card--front" aria-label="Business card front">
    <svg class="card__bands" viewBox="0 0 600 343" width="600" height="343" aria-hidden="true">
      <polygon points="0,0 600,0 0,42"/>
      <polygon points="600,299 600,343 0,343"/>
    </svg>

    <div class="wordmark">VANTRELL</div>
    <div class="tagline">Shaping What Runs Next</div>

    <div class="divider"></div>
    <div class="divider__accent"></div>

    <div class="contact">
      <p class="contact__name">MAREK ELLISON</p>
      <p class="contact__title">V.P. of Governmental Affairs</p>
      <p class="contact__address">4120 Alder Ridge Road<br>Fairbanks, Alaska 34812</p>
      <ul class="contact__list">
        <li class="contact__item">
          <svg class="contact__icon" viewBox="0 0 24 24" aria-hidden="true"><path d="M6.6 10.8a15.1 15.1 0 0 0 6.6 6.6l2.2-2.2c.3-.3.7-.4 1-.2 1.1.4 2.3.6 3.6.6.6 0 1 .4 1 1V20c0 .6-.4 1-1 1C10.6 21 3 13.4 3 4c0-.6.4-1 1-1h3.5c.6 0 1 .4 1 1 0 1.3.2 2.5.6 3.6.1.3 0 .7-.2 1z"/></svg>
          555 210 4471
        </li>
        <li class="contact__item">
          <svg class="contact__icon" viewBox="0 0 24 24" aria-hidden="true"><path d="M7 1h10a2 2 0 0 1 2 2v18a2 2 0 0 1-2 2H7a2 2 0 0 1-2-2V3a2 2 0 0 1 2-2zm0 3v14h10V4zm5 15.5a1 1 0 1 0 0 2 1 1 0 0 0 0-2z"/></svg>
          555 318 2096
        </li>
        <li class="contact__item">
          <svg class="contact__icon" viewBox="0 0 24 24" aria-hidden="true"><path d="M2 6h20v12H2zm2 1.5v.4l8 5 8-5v-.4z"/></svg>
          marek@vantrellforge.com
        </li>
        <li class="contact__item">
          <svg class="contact__icon" viewBox="0 0 24 24" aria-hidden="true"><circle cx="12" cy="12" r="10"/></svg>
          www.vantrellforge.com
        </li>
      </ul>
    </div>
  </section>

  <section class="card card--back" aria-label="Business card back">
    <div class="lockup">
      <div class="lockup__mark">
        <span class="lockup__wordmark">VANTRELL</span>
        <span class="lockup__tagline">Shaping What Runs Next</span>
      </div>
      <p class="lockup__company">Vantrell<br>Forge<br>Works<span class="lockup__suffix">INC</span></p>
    </div>
  </section>

</main>
</body>
</html>
```